Business card design for holistic health care clinic

We need a double-sided business card design for our holistic health care clinic that integrates our logo design and also its color scheme. My business is called Valmira. It is an integrative medicine clinic. You have already done the logo for me. Please ensure an elegant and upscale design that is not cluttered, but still has all the necessary information (please see below for details).

Target Market(s)

Wellness, fitness, rehabilitation for educated, well-traveled open-minded clients who are focused on natural, organic, balanced and preventive healthcare and lifestyle.

Industry/Entity Type

Medical

Contact Information for Business Card

Modern, clean.

Number of Pages Required

1 page

Font styles to use
Serif
Sans Serif

Colors

Designer to choose colors to be used in the design.

Requirements
Must have
• Logo on one side, all other information on the other side.
• Other information should include:
• Tobias Wrenfeld - DOE, CPT, LMT
• 4100 East Marrow Drive
• Austin, TX 78119
• 512 555 0148
• 818 555 0192
• info@ValmiraHealth.example
• t.wrenfeld@ValmiraHealth.example
Nice to have
• Darker background on front - but not totally black - shaded/dark gray.

```html
<!DOCTYPE html>
<html lang="en">
<head>
<meta charset="utf-8">
<title>Valmira Business Card</title>
<link rel="stylesheet" href="https://fonts.googleapis.com/css2?family=Montserrat:wght@300;400;600;700;800&display=swap">
<style>
  :root {
    --brand-blue: #1a8fd0;
    --charcoal: #2b2b2d;
    --ink: #222222;
    --muted: #6b6b6b;
    --paper: #ffffff;
    --backdrop: #e9ebee;
  }
  * { box-sizing: border-box; margin: 0; padding: 0; }
  html, body { width: 1200px; height: 852px; overflow: hidden; }
  body {
    background: var(--backdrop);
    font-family: "Montserrat", sans-serif;
    display: flex;
    align-items: center;
    justify-content: center;
    gap: 40px;
  }
  .card {
    position: relative;
    width: 540px;
    height: 309px;
    border-radius: 16px;
    overflow: hidden;
    box-shadow: 0 6px 18px rgba(0,0,0,0.15);
  }
  .card--back {
    background: var(--charcoal);
    display: flex;
    align-items: center;
    justify-content: center;
  }
  .wordmark {
    display: flex;
    align-items: center;
    gap: 12px;
    color: var(--brand-blue);
    font-weight: 800;
    letter-spacing: 1px;
    text-transform: uppercase;
  }
  .wordmark__dot {
    border-radius: 50%;
    background: var(--brand-blue);
  }
  .card--back .wordmark { font-size: 60px; }
  .card--back .wordmark__dot { width: 18px; height: 18px; }

  .card--front { background: var(--paper); }
  .front__wave { position: absolute; inset: 0; width: 100%; height: 100%; }
  .card--front .wordmark {
    position: absolute;
    left: 30px;
    top: 168px;
    font-size: 40px;
  }
  .card--front .wordmark__dot { width: 12px; height: 12px; }

  .person {
    position: absolute;
    right: 28px;
    top: 150px;
    text-align: right;
  }
  .person__name {
    color: var(--brand-blue);
    font-weight: 800;
    font-size: 19px;
    text-transform: uppercase;
    letter-spacing: 0.3px;
  }
  .person__creds {
    color: var(--muted);
    font-size: 10px;
    font-weight: 400;
    margin-top: 2px;
  }
  .person__rule {
    width: 205px;
    height: 1px;
    background: var(--brand-blue);
    margin: 6px 0 0 auto;
  }
  .address {
    position: absolute;
    right: 28px;
    top: 214px;
    text-align: right;
    color: var(--ink);
    font-size: 11px;
    font-weight: 300;
    line-height: 1.45;
  }
  .contacts {
    position: absolute;
    left: 30px;
    top: 226px;
    list-style: none;
    border-top: 1px solid var(--brand-blue);
    padding-top: 7px;
    width: 230px;
  }
  .contacts__item {
    display: flex;
    align-items: center;
    gap: 8px;
    color: var(--ink);
    font-size: 10.5px;
    font-weight: 300;
    line-height: 1.55;
  }
  .contacts__icon { width: 9px; height: 9px; flex: none; }
</style>
</head>
<body>

  <section class="card card--back" aria-label="Card back">
    <div class="wordmark"><span class="wordmark__dot"></span>Valmira</div>
  </section>

  <section class="card card--front" aria-label="Card front">
    <svg class="front__wave" viewBox="0 0 540 309" preserveAspectRatio="none" aria-hidden="true">
      <path fill="var(--brand-blue)" d="M0,0 H540 V52 C470,64 405,132 285,134 C185,136 95,68 0,92 Z"/>
      <path fill="none" stroke="var(--charcoal)" stroke-width="6" d="M540,64 C470,78 405,146 285,148 C185,150 95,82 0,106"/>
    </svg>

    <div class="wordmark"><span class="wordmark__dot"></span>Valmira</div>

    <div class="person">
      <p class="person__name">Tobias Wrenfeld</p>
      <p class="person__creds">DOE, CPT, LMT</p>
      <div class="person__rule"></div>
    </div>

    <address class="address" style="font-style:normal">
      4100 East Marrow Drive<br>
      Austin, TX 78119
    </address>

    <ul class="contacts">
      <li class="contacts__item">
        <svg class="contacts__icon" viewBox="0 0 10 10" aria-hidden="true"><path fill="var(--brand-blue)" d="M2,0.5 L3.6,0.5 L4.2,3 L3,3.8 C3.6,5.2 4.8,6.4 6.2,7 L7,5.8 L9.5,6.4 L9.5,8 C9.5,9 8.8,9.5 8,9.5 C4,9.2 0.8,6 0.5,2 C0.5,1.2 1,0.5 2,0.5 Z"/></svg>
        512 555 0148
      </li>
      <li class="contacts__item">
        <svg class="contacts__icon" viewBox="0 0 10 10" aria-hidden="true"><rect x="2.5" y="0.5" width="5" height="9" rx="1" fill="none" stroke="var(--brand-blue)" stroke-width="1.2"/><circle cx="5" cy="8" r="0.6" fill="var(--brand-blue)"/></svg>
        818 555 0192
      </li>
      <li class="contacts__item">
        <svg class="contacts__icon" viewBox="0 0 10 10" aria-hidden="true"><rect x="0.6" y="2" width="8.8" height="6" fill="none" stroke="var(--brand-blue)" stroke-width="1.1"/><path d="M0.6,2 L5,5.6 L9.4,2" fill="none" stroke="var(--brand-blue)" stroke-width="1.1"/></svg>
        info@ValmiraHealth.example
      </li>
      <li class="contacts__item">
        <svg class="contacts__icon" viewBox="0 0 10 10" aria-hidden="true"><circle cx="5" cy="5" r="4.3" fill="none" stroke="var(--brand-blue)" stroke-width="1"/><ellipse cx="5" cy="5" rx="1.8" ry="4.3" fill="none" stroke="var(--brand-blue)" stroke-width="0.9"/><path d="M0.7,5 H9.3" stroke="var(--brand-blue)" stroke-width="0.9"/></svg>
        t.wrenfeld@ValmiraHealth.example
      </li>
    </ul>
  </section>

</body>
</html>
```